Brightway Haul & Upkeep Services, are a company that offers a 'one stop shop' pre-move clean up a

I have already selected a logo which I would like on the front of the business cards along with phone numbers, web address and email which are:
0487650392
www.brightwayhaul.com.au
brightwayhaulandupkeep@mailbox.example

On the back of the card I would like to list some of the types of service we offer (clean - move - repairs/maintenance) which are:
CLEAN - windows, gutters, solar panels, driveways/paths, carpets.
MOVE - Small/medium size house/office moves, large item pick-up & delivery, yard clean-up and removal.
General maintenance and repairs.

I would like the blue logo on a gray background.

Thanks

```html
<!DOCTYPE html>
<html lang="en">
<head>
<meta charset="utf-8">
<title>Brightway Haul & Upkeep Services – Business Card</title>
<link rel="stylesheet" href="https://fonts.googleapis.com/css2?family=Jost:wght@400;500;700&display=swap">
<style>
  :root {
    --stage: #e9e6e2;
    --card-light: #e6e7e9;
    --card-mid: #c9cbce;
    --brand-blue: #2a6fb8;
    --ink: #2b2b2b;
    --white: #ffffff;
  }
  * { box-sizing: border-box; margin: 0; padding: 0; }
  html, body {
    width: 1200px; height: 682px; overflow: hidden;
    background: var(--stage);
    font-family: "Jost", Arial, sans-serif;
  }
  .stage {
    position: relative; width: 1200px; height: 682px;
    display: flex; align-items: center; justify-content: center; gap: 40px;
  }
  .card {
    position: relative; width: 540px; height: 309px;
    border-radius: 18px; overflow: hidden;
    background: linear-gradient(160deg, var(--card-light) 0%, var(--card-mid) 100%);
    box-shadow: 0 6px 18px rgba(0,0,0,0.25);
  }
  .brand-name {
    color: var(--brand-blue); font-weight: 700; line-height: 1.05;
    text-transform: uppercase; letter-spacing: 0.5px;
  }
  .brand-mark {
    display: inline-block; width: 22px; height: 22px;
    background: var(--brand-blue); border-radius: 50%;
    vertical-align: middle; margin-right: 10px;
  }

  /* Front */
  .card-front .brand-name {
    position: absolute; left: 40px; top: 50px; width: 460px; font-size: 34px;
  }
  .contact-band {
    position: absolute; left: 0; right: 0; top: 178px; height: 66px;
    background: var(--brand-blue); color: var(--white);
    display: flex; align-items: center; justify-content: center; gap: 18px;
    font-size: 15px; font-weight: 400;
  }
  .contact-item { display: flex; align-items: center; gap: 7px; }
  .contact-divider { width: 1px; height: 28px; background: rgba(255,255,255,0.7); }
  .contact-icon { width: 14px; height: 14px; fill: var(--white); }
  .web-address {
    position: absolute; left: 0; right: 0; top: 262px; text-align: center;
    color: var(--ink); font-size: 15px; letter-spacing: 4px;
  }

  /* Back */
  .card-back .brand-name {
    position: absolute; left: 48px; top: 38px; width: 450px; font-size: 32px;
  }
  .services-title {
    position: absolute; left: 0; right: 0; top: 150px; text-align: center;
    color: var(--brand-blue); font-size: 24px; font-weight: 500; letter-spacing: 6px;
  }
  .services-list {
    position: absolute; left: 0; right: 0; top: 194px; list-style: none;
    text-align: center; color: var(--ink); font-size: 19px; font-weight: 500;
    text-transform: uppercase; line-height: 1.55;
  }
  .services-list .bullet { color: var(--brand-blue); margin-right: 6px; }
</style>
</head>
<body>
<main class="stage">
  <section class="card card-front">
    <div class="brand-name"><span class="brand-mark"></span>Brightway Haul &amp; Upkeep Services</div>
    <div class="contact-band">
      <span class="contact-item">
        <svg class="contact-icon" viewBox="0 0 24 24" aria-hidden="true"><path d="M6.6 10.8a15.1 15.1 0 0 0 6.6 6.6l2.2-2.2a1 1 0 0 1 1-.25 11.4 11.4 0 0 0 3.6.57 1 1 0 0 1 1 1V20a1 1 0 0 1-1 1A17 17 0 0 1 3 4a1 1 0 0 1 1-1h3.5a1 1 0 0 1 1 1c0 1.25.2 2.45.57 3.6a1 1 0 0 1-.25 1z"/></svg>
        0487650392
      </span>
      <span class="contact-divider"></span>
      <span class="contact-item">
        <svg class="contact-icon" viewBox="0 0 24 24" aria-hidden="true"><path d="M2 5h20v14H2z M3.5 6.5 12 13l8.5-6.5" fill="none" stroke="#fff" stroke-width="2"/></svg>
        brightwayhaulandupkeep@mailbox.example
      </span>
    </div>
    <div class="web-address">www.brightwayhaul.com.au</div>
  </section>

  <section class="card card-back">
    <div class="brand-name"><span class="brand-mark"></span>Brightway Haul &amp; Upkeep Services</div>
    <h2 class="services-title">Services we offer</h2>
    <ul class="services-list">
      <li><span class="bullet">•</span>Clean &nbsp;<span class="bullet">•</span>Move</li>
      <li><span class="bullet">•</span>General maintenance and repairs.</li>
    </ul>
  </section>
</main>
</body>
</html>
```